New Baby Formula Company Needs a Shopify Website Design

We are launching a baby formula company and need a Shopify website design. We have a patented product that is a disposable pouch with a frangible seal through the middle. The top half contains formula powder and the bottom half contains purified water. There is also a bottle nipple on the corner under the cap in order to feed the baby. You just need to squeeze the bottom half of the pouch to break the seal and then the water and formula will mix. You then only need to shake it and then remove the cap and feed the baby. We will also sell formula in containers like the other formula companies. We want this website to stand out and look professional. We don't want a boring layout, but something unique and captivating. I have attached a mockup rendering of our product, though it's not the finished product and our logo. This will let you know the color scheme we are going for. Let me know if you have any further questions. Thank you

```html
<!DOCTYPE html>
<html lang="en">
<head>
<meta charset="utf-8">
<title>Milvana Baby — Infant Formula</title>
<link rel="stylesheet" href="https://fonts.googleapis.com/css2?family=Poppins:wght@400;500;600;700&family=Lato:wght@400;700&display=swap">
<style>
:root{
  --olive:#a2b02c;
  --olive-dark:#8d9a22;
  --ink:#1e1e20;
  --panel:#252527;
  --product-bg:#2a2c20;
  --white:#ffffff;
  --muted:#e9e9e9;
  --line:#3a3a3c;
}
*{margin:0;padding:0;box-sizing:border-box}
html,body{width:1200px;height:2918px;overflow:hidden}
body{background:var(--ink);color:var(--white);font-family:'Lato',sans-serif;position:relative}
.abs{position:absolute}
.topbar{left:0;top:0;width:1200px;height:43px;background:var(--olive);font-size:12px;display:flex;align-items:center;justify-content:center}
.brand{display:flex;align-items:center;gap:8px;color:var(--olive);font-family:'Poppins',sans-serif;font-weight:600;font-size:17px}
.brand-dot{width:22px;height:22px;border:2px solid var(--olive);border-radius:50%}
.nav{left:394px;top:96px;display:flex;gap:40px;font-size:15px;letter-spacing:.2px}
.nav a{color:var(--white);text-decoration:none}
.icons{left:1026px;top:93px;display:flex;gap:22px}
.cart-count{left:1086px;top:87px;font-size:8px;color:var(--olive)}
h1,h2,h3{font-family:'Poppins',sans-serif}
.hero-title{left:111px;top:248px;font-size:49px;font-weight:400;line-height:68px}
.hero-title strong{color:var(--olive);font-weight:700;display:block}
.hero-sub{left:111px;top:473px;width:400px;font-size:21px;line-height:33px}
.btn{background:var(--olive);color:var(--white);font-family:'Poppins',sans-serif;font-weight:600;font-size:15px;display:flex;align-items:center;justify-content:center;text-decoration:none}
.photo{display:block}
.sec-title{font-size:35px;font-weight:600}
.body-text{font-size:14.5px;line-height:24px;color:var(--muted)}
.price{font-family:'Poppins',sans-serif;color:var(--olive);font-size:22px;font-weight:600}
.gallery-card{background:var(--panel)}
.newsletter{left:0;top:2238px;width:1200px;height:300px;background:var(--olive);text-align:center}
.newsletter h2{font-size:38px;font-weight:600;margin-top:50px}
.newsletter p{font-size:17px;margin-top:14px}
.email{position:absolute;left:407px;top:182px;width:386px;height:61px;border:2px solid var(--white);display:flex;align-items:center;justify-content:space-between;padding:0 16px;font-size:17px}
.foot-links{list-style:none;font-size:15px;line-height:26px}
.payments{left:458px;top:2817px;display:flex;gap:4px}
.pay{width:44px;height:25px;border-radius:3px}
</style>
</head>
<body>
<div class="abs topbar">Nemo enim ipsam voluptatem quia voluptas</div>

<div class="abs brand" style="left:113px;top:95px"><span class="brand-dot"></span>Milvana Baby</div>
<nav class="abs nav"><a href="#">HOME</a><a href="#">ABOUT US</a><a href="#">PRODUCTS</a><a href="#">GALLERY</a></nav>
<div class="abs icons">
  <svg width="20" height="20" viewBox="0 0 20 20" fill="none" stroke="#a2b02c" stroke-width="2.4"><circle cx="8" cy="8" r="6"/><path d="M12.5 12.5L18 18"/></svg>
  <svg width="20" height="20" viewBox="0 0 20 20" fill="#a2b02c"><path d="M1 2h3l3 10h10l2-7H6" stroke="#a2b02c" stroke-width="2" fill="none"/><circle cx="8" cy="17" r="1.8"/><circle cx="16" cy="17" r="1.8"/></svg>
</div>
<div class="abs cart-count">(0)</div>

<h1 class="abs hero-title">Infant Formula<strong>Milk-Based Powder</strong>With Purified Water</h1>
<p class="abs hero-sub">Easy Digestion Immune Support Brain &amp; Gut Health</p>
<a class="abs btn" href="#" style="left:111px;top:577px;width:112px;height:45px">Shop Now</a>
<div class="abs photo" role="img" aria-label="Formula powder poured from a pouch into a glass of milk" style="left:600px;top:185px;width:489px;height:512px;background:linear-gradient(135deg,#f2f2f0,#d9d6d0 60%,#b8afa4)"></div>

<div class="abs photo" role="img" aria-label="Baby drinking from a bottle" style="left:111px;top:800px;width:295px;height:420px;background:linear-gradient(160deg,#eceae8,#c9b3a3 55%,#e6e2de)"></div>
<div class="abs photo" role="img" aria-label="Formula pouch with a scoop of powder" style="left:406px;top:800px;width:293px;height:420px;background:radial-gradient(circle at 55% 45%,#f3f1e6 0,#e3e6c9 30%,#a2b02c 58%)"></div>
<h2 class="abs sec-title" style="left:760px;top:872px">About Milvana Baby</h2>
<p class="abs body-text" style="left:760px;top:944px;width:335px">Lorem ipsum dolor sit amet, consectetur adipiscing elit, sed do eiusmod tempor incididunt ut labore et dolore magna aliqua. Ut enim ad minim veniam, quis nostrud exercitation ullamco laboris nisi ut aliquip ex ea commodo consequat. Duis aute irure dolor in reprehenderit in voluptate velit esse cillum dolore eu fugiat nulla pariatur. Excepteur sint occaecat cupidatat non proident, sunt in culpa qui officia deserunt mollit anim id est laborum.</p>

<h2 class="abs sec-title" style="left:116px;top:1350px">Our Product</h2>
<div class="abs price" style="left:116px;top:1408px">$133</div>
<p class="abs body-text" style="left:116px;top:1455px;width:375px">Lorem ipsum dolor sit amet, consectetur adipiscing elit, sed do eiusmod tempor incididunt ut labore et dolore magna aliqua. Ut enim ad minim veniam, quis nostrud exercitation ullamco laboris nisi ut aliquip ex ea commodo consequat. Duis aute irure dolor in reprehenderit in voluptate velit esse cillum dolore eu fugiat nulla pariatur. Excepteur sint occaecat cupidatat non proident, sunt in culpa qui officia deserunt mollit anim id est laborum.</p>
<a class="abs btn" href="#" style="left:117px;top:1647px;width:111px;height:46px">Shop Now</a>
<div class="abs photo" role="img" aria-label="Front and back of the formula pouch" style="left:600px;top:1322px;width:489px;height:409px;background:radial-gradient(ellipse at 50% 45%,#e4e7cf 0,#b8c46a 28%,#2a2c20 62%)"></div>

<div class="abs gallery-card" style="left:112px;top:1835px;width:306px;height:299px"></div>
<h3 class="abs" style="left:142px;top:1873px;font-size:24px;font-weight:600">Our Gallery</h3>
<p class="abs body-text" style="left:142px;top:1926px;width:250px">Lorem ipsum dolor sit amet, consectetur adipiscing elit, sed do eiusmod tempor incididunt ut labore et dolore magna aliqua.</p>
<a class="abs" href="#" style="left:142px;top:2040px;color:var(--olive);font-family:'Poppins',sans-serif;font-weight:600;font-size:16px;text-decoration:none;display:flex;align-items:center;gap:5px">View All <svg width="14" height="14" viewBox="0 0 14 14"><circle cx="7" cy="7" r="7" fill="#a2b02c"/><path d="M5 3.5L8.5 7 5 10.5" stroke="#1e1e20" stroke-width="2" fill="none"/></svg></a>
<div class="abs photo" role="img" aria-label="Glass of milk with wooden spoons of powder" style="left:449px;top:1835px;width:306px;height:299px;background:linear-gradient(135deg,#d8c3a5,#f1ece3 50%,#c9a981)"></div>
<div class="abs photo" role="img" aria-label="Scoop of formula added to a baby bottle" style="left:783px;top:1835px;width:306px;height:299px;background:linear-gradient(135deg,#b9a497,#e9e6e4 50%,#9c9a9a)"></div>

<section class="abs newsletter">
  <h2>Sign up our Newsletter</h2>
  <p>Lorem ipsum dolor sit amet, consectetur adipiscing</p>
  <div class="email"><span>Email</span><svg width="26" height="14" viewBox="0 0 26 14" fill="none" stroke="#fff" stroke-width="1.6"><path d="M0 7h24M18 1l6 6-6 6"/></svg></div>
</section>

<h3 class="abs" style="left:111px;top:2600px;font-size:19px;font-weight:600">About Milvana Baby</h3>
<ul class="abs foot-links" style="left:111px;top:2638px"><li>Home</li><li>About Us</li><li>Products</li><li>Gallery</li></ul>
<div class="abs brand" style="left:717px;top:2647px;font-size:20px"><span class="brand-dot" style="width:26px;height:26px"></span>Milvana</div>
<p class="abs" style="left:853px;top:2631px;width:250px;font-size:15px;line-height:26px">Lorem ipsum dolor sit amet, consectetur adipiscing elit, sed do eiusmod tempor</p>
<div class="abs" style="left:714px;top:2737px;display:flex;gap:20px">
  <span style="width:20px;height:20px;border-radius:50%;background:#fff"></span>
  <span style="width:20px;height:20px;border-radius:50%;background:#fff"></span>
  <span style="width:20px;height:20px;border-radius:50%;background:#fff"></span>
</div>
<div class="abs" style="left:111px;top:2793px;width:978px;height:1px;background:var(--line)"></div>
<div class="abs payments">
  <span class="pay" style="background:#e8e3d6"></span>
  <span class="pay" style="background:#f1f1f1"></span>
  <span class="pay" style="background:#eef0f6"></span>
  <span class="pay" style="background:#f4f4f4"></span>
  <span class="pay" style="background:#3b7fc4"></span>
  <span class="pay" style="background:#c9342e"></span>
</div>
<p class="abs" style="left:0;top:2864px;width:1200px;text-align:center;font-size:14.5px">©Copyrights 2024 Company Name &nbsp;| &nbsp; All Rights Reserved</p>
</body>
</html>
```